Business Card Design Project

I need a business card designed from scratch. I have an existing logo that I can upload in Illustrator for modification or redesign.

The Company is called Query Lanterns http://querylanterns.com.au and we provide Search Engine Optimization services to Australian businesses. The current logo signifies an increase in visitors, profits etc...

There are no restrictions as to the redesign - colours, style etc are all open to change.

Cards will be full colour and one sided printed at http://www.cardmoxel.com.au so check their requirements for file format and sizes etc.

I will expect all original files upon completion of project.

Target Market(s)

Any business with a web site looking to improve their search engine rankings

Industry/Entity Type

Business

Requirements
Must have
• I like modern, sleek designs. Clean, not fussy, uncluttered.

```html
<!DOCTYPE html>
<html lang="en">
<head>
<meta charset="utf-8">
<title>Query Lanterns Business Card</title>
<link rel="stylesheet" href="https://fonts.googleapis.com/css2?family=PT+Sans:wght@400;700&display=swap">
<style>
  :root {
    --backdrop: #ebe8e4;
    --brand-blue: #1f5fa8;
    --deep-blue: #153f78;
    --glow-blue: #2f7cc6;
    --accent-yellow: #f5b81c;
    --paper: #ffffff;
    --ink: #3a3a3a;
  }
  * { box-sizing: border-box; margin: 0; padding: 0; }
  html, body {
    width: 1200px; height: 412px; overflow: hidden;
    background: var(--backdrop);
    font-family: "PT Sans", sans-serif;
  }
  .canvas { position: relative; width: 1200px; height: 412px; }
  .card {
    position: absolute; top: 64px; width: 498px; height: 285px;
    overflow: hidden;
    box-shadow: 0 3px 10px rgba(0,0,0,0.25);
  }
  .card--front { left: 72px; }
  .card--back {
    left: 632px;
    background: radial-gradient(ellipse at 45% 45%, var(--glow-blue) 0%, var(--brand-blue) 45%, var(--deep-blue) 100%);
  }
  .front-shapes { position: absolute; inset: 0; width: 100%; height: 100%; }

  .wordmark {
    position: absolute; display: flex; align-items: center; gap: 10px;
    font-weight: 700; letter-spacing: -0.5px; line-height: 1;
  }
  .wordmark__dot { width: 20px; height: 20px; border-radius: 50%; background: var(--accent-yellow); }
  .card--front .wordmark { left: 34px; top: 50px; font-size: 36px; color: var(--brand-blue); }
  .card--back .wordmark { left: 0; right: 0; top: 112px; justify-content: center; font-size: 38px; color: var(--paper); }

  .holder { position: absolute; left: 33px; top: 186px; color: var(--ink); }
  .holder__name { font-size: 17px; font-weight: 700; }
  .holder__title { font-size: 15px; font-weight: 400; }
  .holder__address { margin-top: 24px; font-size: 13px; line-height: 17px; }

  .contacts {
    position: absolute; right: 14px; top: 204px;
    list-style: none; text-align: right; color: var(--paper);
    font-size: 12.5px; line-height: 17.5px;
  }
  .contacts li { display: flex; justify-content: flex-end; align-items: center; gap: 6px; }
  .contacts svg { width: 10px; height: 10px; fill: var(--paper); }

  .back-url {
    position: absolute; left: 0; right: 0; top: 222px; text-align: center;
    color: var(--paper); font-size: 12.5px; font-weight: 700; letter-spacing: 2.6px;
  }
</style>
</head>
<body>
<main class="canvas">
  <section class="card card--front" aria-label="Card front">
    <svg class="front-shapes" viewBox="0 0 498 285" preserveAspectRatio="none" aria-hidden="true">
      <defs>
        <radialGradient id="frontBlue" cx="0.7" cy="0.55" r="0.7">
          <stop offset="0" stop-color="#2a72bd"/>
          <stop offset="1" stop-color="#163f7a"/>
        </radialGradient>
        <linearGradient id="paperShade" x1="0" y1="0" x2="1" y2="1">
          <stop offset="0" stop-color="#ffffff"/>
          <stop offset="1" stop-color="#eeeeee"/>
        </linearGradient>
      </defs>
      <rect width="498" height="285" fill="url(#frontBlue)"/>
      <path d="M0,0 H498 V18 C478,150 340,262 150,285 H0 Z" fill="#f5b81c"/>
      <path d="M0,0 H468 C446,145 330,255 160,285 H0 Z" fill="url(#paperShade)"/>
    </svg>

    <div class="wordmark"><span class="wordmark__dot"></span>Query Lanterns</div>

    <div class="holder">
      <p><span class="holder__name">Your Name /</span> <span class="holder__title">Title</span></p>
      <p class="holder__address">Complex name,Street name<br>City, State, zip code</p>
    </div>

    <ul class="contacts">
      <li>098 765 4321 <svg viewBox="0 0 10 10"><path d="M2 0.5 L4 2.5 L3 3.8 C3.8 5.4 4.6 6.2 6.2 7 L7.5 6 L9.5 8 L8 9.5 C4 9 1 6 0.5 2 Z"/></svg></li>
      <li>098 765 4321 <svg viewBox="0 0 10 10"><path d="M3 0 H7 V10 H3 Z M3.8 1.2 V6.5 H6.2 V1.2 Z" fill-rule="evenodd"/></svg></li>
      <li>enquiry@querylanterns.com.au <svg viewBox="0 0 10 10"><path d="M0 2 H10 V8.5 H0 Z M0.8 2.6 L5 5.6 L9.2 2.6" fill-rule="evenodd"/></svg></li>
      <li>www.querylanterns.com.au <svg viewBox="0 0 10 10"><circle cx="5" cy="5" r="4.5"/></svg></li>
    </ul>
  </section>

  <section class="card card--back" aria-label="Card back">
    <div class="wordmark"><span class="wordmark__dot"></span>Query Lanterns</div>
    <p class="back-url">www.querylanterns.com.au</p>
  </section>
</main>
</body>
</html>
```